MRT Property - Business Cards

Looking for a business card & general letterhead, signage etc design for our new logo.

Colours:
000a20
0056a2
00b5ef
0088ce
68cef2

Fonts:
Poppins
Karla

Please keep look and feel of new brand - example in the zip package I sent.

```html
<!DOCTYPE html>
<html lang="en">
<head>
<meta charset="utf-8">
<title>MRT Property – Business Cards</title>
<link rel="stylesheet" href="https://fonts.googleapis.com/css2?family=Delius&family=Montserrat:wght@400;500&family=Poppins:wght@600&display=swap">
<style>
  :root {
    --ink: #000a20;
    --text: #1c1f26;
    --brand-navy: #0056a2;
    --brand-sky: #00b5ef;
    --brand-mid: #0088ce;
    --brand-pale: #68cef2;
    --card-back: #0b56a3;
    --paper: #ffffff;
    --stage: #e8e5e0;
  }
  * { margin: 0; padding: 0; box-sizing: border-box; }
  html, body {
    width: 900px; height: 1200px; overflow: hidden;
    background: var(--stage);
  }
  .canvas { position: relative; width: 900px; height: 1200px; }

  .card {
    position: absolute;
    border-radius: 22px;
    overflow: hidden;
    box-shadow: 0 6px 14px rgba(0, 10, 32, 0.25);
  }
  .card--front { left: 80px; top: 131px; width: 742px; height: 440px; background: var(--paper); }
  .card--back  { left: 78px; top: 638px; width: 744px; height: 440px; background: var(--card-back); }

  .wordmark {
    position: absolute;
    font-family: "Poppins", sans-serif;
    font-weight: 600;
    white-space: nowrap;
    line-height: 1;
  }
  .card--front .wordmark { left: 66px; top: 210px; font-size: 40px; color: var(--brand-navy); }
  .card--back .wordmark  { right: 70px; top: 300px; font-size: 62px; color: var(--paper); }

  .divider {
    position: absolute; left: 354px; top: 109px;
    width: 2px; height: 223px; background: var(--brand-navy);
  }

  .contact { position: absolute; left: 371px; top: 105px; font-family: "Montserrat", sans-serif; color: var(--text); }
  .contact__name {
    font-family: "Delius", cursive;
    font-size: 31px; color: var(--brand-navy); line-height: 1.1;
  }
  .contact__role { font-size: 15px; margin-top: 6px; }
  .contact__address { font-size: 15px; line-height: 21px; margin-top: 23px; }
  .contact__list { list-style: none; margin-top: 20px; font-size: 15px; }
  .contact__list li { display: flex; align-items: center; gap: 12px; height: 28px; }
  .contact__list svg { width: 15px; height: 15px; fill: var(--brand-navy); flex: none; }

  .colour-band { position: absolute; left: 0; bottom: 0; width: 100%; height: 18px; display: flex; }
  .colour-band span { flex: 1; }
  .colour-band .pale { background: var(--brand-pale); }
  .colour-band .sky  { background: var(--brand-sky); }
  .colour-band .mid  { background: var(--brand-mid); }
  .colour-band .navy { background: var(--brand-navy); }
</style>
</head>
<body>
<main class="canvas">
  <section class="card card--front" aria-label="Business card front">
    <div class="wordmark">MRT Property</div>
    <div class="divider"></div>
    <div class="contact">
      <p class="contact__name">Dana Whitlow</p>
      <p class="contact__role">Mnaging Director</p>
      <p class="contact__address">482 Maple Ridge Ave Suite<br>210 Dayton Ohio 45402</p>
      <ul class="contact__list">
        <li>
          <svg viewBox="0 0 24 24" aria-hidden="true"><path d="M6.6 10.8a15.1 15.1 0 0 0 6.6 6.6l2.2-2.2a1 1 0 0 1 1-.25 11.4 11.4 0 0 0 3.6.57 1 1 0 0 1 1 1V20a1 1 0 0 1-1 1A17 17 0 0 1 3 4a1 1 0 0 1 1-1h3.5a1 1 0 0 1 1 1c0 1.25.2 2.45.57 3.57a1 1 0 0 1-.25 1z"/></svg>
          1 (555) 014-2290
        </li>
        <li>
          <svg viewBox="0 0 24 24" aria-hidden="true"><path d="M2 5h20v2l-10 6L2 7z"/><path d="M2 9l10 6 10-6v10H2z"/></svg>
          info@mrtproperty.com
        </li>
        <li>
          <svg viewBox="0 0 24 24" aria-hidden="true"><circle cx="12" cy="12" r="10"/><path d="M5 8c3 0 4 2 3 4s1 3 2 5l-1 3M14 3c-1 2 1 3 3 3s2 3 0 4-1 4 1 5" stroke="#fff" stroke-width="1.6" fill="none"/></svg>
          www.mrtproperty.com
        </li>
      </ul>
    </div>
    <div class="colour-band" aria-hidden="true">
      <span class="pale"></span><span class="sky"></span><span class="mid"></span><span class="navy"></span>
    </div>
  </section>

  <section class="card card--back" aria-label="Business card back">
    <div class="wordmark">MRT Property</div>
  </section>
</main>
</body>
</html>
```